New Fun, Positive, energised looking Business Card Needed for High Achiever Coach

I am looking for a two sided full colour business card. I am self employed and have recently re branded my 1-2-1 work re-vitalising high achievers. My target client base for these cards is therefore high achievers - usually aged 40 -55, they are often entrepreneurs, CEO or work in banking and finance and 2/3 are male. I work with them on 90 day or 6 month coaching programs to help them live their success in a healthier, more sustainable and fulfiiled way. They pay for this privately so though they are corporate types the cards need not look 'corporate'. I want to portray the idea of transformation, vitality and re-connecting.
You can get a feel for the look I like on my new website: morvenlisk.co.uk
I want to use this logo with strapline (Re-Vitalising High Achievers) (I purchased off Logoharbor) and font/ colours (the turquoise and green).
Details to include on the card:
www.morvenlisk.co.uk
+44 7915 302618
morven@morvenlisk.co.uk
skype: morvenlisk
I'd also like to include:
Do you struggle to switch off? Want to be healthier and feel fitter? Want closer relationships? More clarity over the direction you are headed? I can help you do these things using integrated mind-body techniques. Visit morvenlisk.co.uk TODAY to apply for a FREE Breakthrough session.
BUT if that is too much text for a card I am open to advice/ammendments.
Updates
Thanks for your design - I am considering them. PLease change the wording to :

```html
<!DOCTYPE html>
<html lang="en">
<head>
<meta charset="utf-8">
<title>Morven Lisk – Business Card</title>
<link rel="stylesheet" href="https://fonts.googleapis.com/css2?family=Open+Sans:wght@400;600;800&display=swap">
<style>
  :root {
    --bg: #e9ecef;
    --card: #050505;
    --turquoise: #00a6c8;
    --green: #5cb85c;
    --white: #ffffff;
    --rule: #8a8a8a;
  }
  * { margin: 0; padding: 0; box-sizing: border-box; }
  html, body { width: 1200px; height: 987px; overflow: hidden; background: var(--bg); }
  body { position: relative; font-family: "Open Sans", Arial, sans-serif; }

  .card {
    position: absolute;
    width: 620px;
    height: 380px;
    background: var(--card);
    border-radius: 36px;
    overflow: hidden;
    color: var(--white);
  }
  .card--back { left: 540px; top: 60px; }
  .card--front { left: 40px; top: 547px; }

  /* Back */
  .pitch {
    position: absolute;
    left: 36px;
    top: 44px;
    width: 560px;
    font-size: 16.5px;
    line-height: 1.45;
  }
  .pitch .link { color: var(--green); font-weight: 600; }
  .back-mark {
    position: absolute;
    right: 40px;
    bottom: 40px;
    display: flex;
    align-items: center;
    gap: 14px;
  }
  .back-mark .dot {
    width: 56px;
    height: 56px;
    border-radius: 50%;
    background: var(--green);
  }
  .back-mark .name {
    font-size: 30px;
    font-weight: 800;
    color: var(--green);
    line-height: 1;
  }

  /* Front */
  .wave { position: absolute; inset: 0; width: 100%; height: 100%; }
  .brand {
    position: absolute;
    left: 36px;
    top: 48px;
    width: 260px;
  }
  .brand-mark {
    width: 48px;
    height: 48px;
    border-radius: 50%;
    background: var(--green);
    margin: 0 0 14px 90px;
  }
  .brand-name {
    font-size: 38px;
    font-weight: 800;
    color: var(--turquoise);
    line-height: 1;
    white-space: nowrap;
  }
  .brand-strapline {
    margin-top: 8px;
    font-size: 15px;
    color: var(--turquoise);
    white-space: nowrap;
  }
  .divider {
    position: absolute;
    left: 316px;
    top: 96px;
    width: 1px;
    height: 110px;
    background: var(--rule);
  }
  .contacts {
    position: absolute;
    left: 334px;
    top: 102px;
    list-style: none;
    font-size: 17px;
  }
  .contacts li { display: flex; align-items: center; gap: 9px; margin-bottom: 12px; white-space: nowrap; }
  .contacts svg { width: 17px; height: 17px; flex: none; }
  .web {
    position: absolute;
    right: 50px;
    bottom: 34px;
    font-size: 24px;
    letter-spacing: 1px;
    color: var(--white);
  }
</style>
</head>
<body>

<section class="card card--back" aria-label="Business card, back">
  <p class="pitch">
    Do you struggle to switch off?<br>
    Want to be healthier and feel fitter?<br>
    Want closer relationships?<br>
    More clarity over the direction you are headed?<br>
    I can help you do these things using integrated mind-body techniques.<br>
    Visit <span class="link">morvenlisk.co.uk</span> TODAY to apply for a FREE Breakthrough session.
  </p>
  <div class="back-mark">
    <span class="dot" aria-hidden="true"></span>
    <span class="name">Morven Lisk</span>
  </div>
</section>

<section class="card card--front" aria-label="Business card, front">
  <svg class="wave" viewBox="0 0 620 380" preserveAspectRatio="none" aria-hidden="true">
    <path d="M0,150 C70,235 260,255 420,295 C520,320 585,350 620,380 L0,380 Z" fill="var(--turquoise)"/>
    <path d="M40,175 C110,250 280,270 440,310 C530,333 580,355 605,380" fill="none" stroke="var(--card)" stroke-width="7"/>
  </svg>

  <div class="brand">
    <div class="brand-mark" aria-hidden="true"></div>
    <div class="brand-name">Morven Lisk</div>
    <div class="brand-strapline">Re-Vitalising High Achievers</div>
  </div>

  <div class="divider"></div>

  <ul class="contacts">
    <li>
      <svg viewBox="0 0 20 20" aria-hidden="true"><circle cx="10" cy="10" r="9" fill="none" stroke="var(--green)" stroke-width="1.6"/><path d="M7 5.5l1.6 2.3-1 1.1c.6 1.3 1.5 2.2 2.8 2.8l1.1-1 2.3 1.6-.8 1.6c-3.6-.3-6.4-3.1-6.7-6.7z" fill="var(--green)"/></svg>
      <span>+44 7915 302618</span>
    </li>
    <li>
      <svg viewBox="0 0 20 20" aria-hidden="true"><rect x="2" y="5" width="16" height="11" rx="1.5" fill="var(--green)"/><path d="M2.5 5.5L10 11l7.5-5.5" fill="none" stroke="var(--card)" stroke-width="1.4"/></svg>
      <span>morven@morvenlisk.co.uk</span>
    </li>
    <li>
      <svg viewBox="0 0 20 20" aria-hidden="true"><circle cx="10" cy="10" r="9" fill="var(--turquoise)"/></svg>
      <span>morvenlisk</span>
    </li>
  </ul>

  <div class="web">www.morvenlisk.co.uk</div>
</section>

</body>
</html>
```